Manufacturer Website with Home and Product page

We have this website, veltaro.com, but we need another one for the Canadian market. Canadians like to deal with Canadians so we need to gear it to that. It will be a simpler website than the current site.

We will need a design for two pages, one for the home page and one for a product page.

I synthesized all the brief information for the designers here, descriptions for both pages are included:

https://files.brimlodge.net/doc/8qwx3Lm2Rt7Yp0KzVb4Nc6HsJd9FgA1eUi5Tr

Supporting Folder:
https://files.brimlodge.net/folder/7ZpqW3nTx8Kd2LmR5vYb0HcJs

Industry/Entity Type

Tanning Beds, Red Light Beds, Hydro massage beds

Number of Pages Required

2 page

Requirements
Must have
• Two page descriptions: https://files.brimlodge.net/doc/8qwx3Lm2Rt7Yp0KzVb4Nc6HsJd9FgA1eUi5Tr/view
Nice to have
• Information Folder: https://files.brimlodge.net/folder/u/0/7ZpqW3nTx8Kd2LmR5vYb0HcJs

```html
<!DOCTYPE html>
<html lang="en">
<head>
<meta charset="utf-8">
<title>Veltaro Canada — Home</title>
<link href="https://fonts.googleapis.com/css2?family=Nunito+Sans:wght@300;400;600;700;800&display=swap" rel="stylesheet">
<style>
:root{
  --brand:#6b77c2;
  --brand-dark:#5763b0;
  --red:#ee1c25;
  --ink:#1b1b24;
  --muted:#555;
  --page:#ffffff;
  --panel:#f4f4f5;
  --salon-bg:#ececee;
  --footer-bg:#e3e3e5;
}
*{box-sizing:border-box;margin:0;padding:0}
html,body{width:1200px;height:2533px;overflow:hidden;background:var(--page)}
body{position:relative;font-family:"Nunito Sans",Arial,sans-serif;color:var(--ink)}
.abs{position:absolute}
.btn{position:absolute;background:var(--red);color:#fff;font-weight:700;font-size:12px;border-radius:6px;display:flex;align-items:center;justify-content:center}

/* header */
.logo{left:47px;top:18px;font-size:32px;font-weight:800;color:var(--brand);letter-spacing:-1px}
.logo-sub{left:70px;top:48px;font-size:6px;letter-spacing:6px;color:var(--brand)}
.nav{left:283px;top:31px;display:flex;gap:26px;font-size:12px;font-weight:700}
.nav span{position:relative}
.nav .active::after{content:"";position:absolute;left:50%;top:18px;width:4px;height:4px;border-radius:50%;background:var(--red);transform:translateX(-50%)}
.caret{color:var(--red);font-size:10px;margin-left:2px}
.phone{left:898px;top:30px;font-size:12px;font-weight:800;display:flex;gap:8px;align-items:center}

/* hero */
.hero{left:8px;top:76px;width:1184px;height:450px;border-radius:12px;overflow:hidden;
  background:linear-gradient(90deg,#8d96d6 0%,#a3abe2 45%,#c2c7ee 75%,#d7d2e6 100%)}
.hero-visual{right:0;top:0;width:690px;height:450px;
  background:radial-gradient(ellipse at 35% 55%,rgba(255,255,255,.55),transparent 55%),radial-gradient(ellipse at 85% 35%,#e9c7b8,transparent 45%)}
.hero-text{left:39px;top:128px;color:#fff;line-height:1.22}
.hero-text .light{font-size:26px;font-weight:300}
.hero-text .big{font-size:33px;font-weight:800}
.hero-text .big em{font-style:normal;font-weight:300}
.counter{left:40px;top:376px;color:#fff;font-size:10px}
.counter .bar{position:absolute;top:18px;left:1px;width:76px;height:1px;background:rgba(255,255,255,.4)}
.counter .bar i{display:block;width:18px;height:2px;background:#fff}
.counter .last{position:absolute;top:34px;left:62px}

.dots{display:flex;gap:6px;position:absolute;left:50%;transform:translateX(-50%)}
.dots i{width:7px;height:7px;border-radius:50%;border:1px solid var(--red)}
.dots i.on{background:var(--red)}

.h2{position:absolute;left:0;width:1200px;text-align:center;color:var(--brand);font-size:27px;font-weight:800;letter-spacing:.3px}

/* featured */
.card{position:absolute;top:633px;width:328px;height:415px;border-radius:6px;overflow:hidden;display:flex;align-items:center;justify-content:center;color:#fff;font-size:36px;font-weight:300}
.card.tan{left:46px;background:linear-gradient(160deg,#e7bde0,#c57bb7 45%,#f0d8ea)}
.card.hydro{left:436px;background:linear-gradient(170deg,#c9a8a0,#8f87c3 45%,#6f6da3);align-items:flex-end;padding-bottom:32px;box-shadow:0 10px 24px rgba(0,0,0,.25)}
.card.red{left:826px;background:linear-gradient(150deg,#ff6a3a,#f2336b 45%,#c9235a)}

/* applications */
.app{position:absolute;top:1173px;height:380px;background:var(--panel);border-radius:6px;overflow:hidden;box-shadow:0 4px 14px rgba(0,0,0,.12)}
.app.left{left:-30px;width:145px}
.app.left p{position:absolute;left:30px;top:88px;font-size:12px;line-height:18.7px;width:200px}
.app.center{left:175px;width:850px}
.app.right{left:1085px;width:160px;background:linear-gradient(120deg,#a86a45,#e4c8b4 60%,#7b4a30)}
.app-img{left:0;top:0;width:420px;height:380px;background:linear-gradient(135deg,#d6d3cf,#b7b1aa 50%,#e7e4e6)}
.app-body{left:465px;top:45px;width:355px}
.app-body h3{font-size:36px;font-weight:300;letter-spacing:.5px;margin-bottom:6px}
.app-body p{font-size:12px;line-height:18.8px}

/* salon */
.salon{left:0;top:1625px;width:1200px;height:563px;background:var(--salon-bg);overflow:hidden}
.salon-l1{left:177px;top:109px;font-size:36px;font-weight:300;color:#333;line-height:36px}
.salon-l2{left:177px;top:150px;font-size:52px;font-weight:800;color:var(--brand);line-height:58px}
.salon-l2 em{font-style:normal;font-weight:300}
.salon-l3{left:177px;top:211px;font-size:27px;font-weight:800;line-height:34px}
.salon-list{left:177px;top:293px;list-style:none}
.salon-list li{font-size:18px;font-weight:700;height:31px;line-height:31px;display:flex;align-items:center;gap:10px}

/* footer */
.footer{left:0;top:2188px;width:1200px;height:247px;background:var(--footer-bg)}
.f-logo{left:45px;top:34px;font-size:36px;font-weight:800;color:var(--ink);letter-spacing:-1px}
.f-addr{left:47px;top:90px;font-size:12px;line-height:15px}
.f-addr b.t{font-size:16px;display:block;margin-bottom:2px}
.f-h{font-size:16px;font-weight:800}
.f-links{list-style:none;font-size:12px}
.f-links li{height:22.7px;display:flex;align-items:center;gap:8px}
.social{left:794px;top:80px;display:flex;gap:9px}
.social i{width:29px;height:29px;border-radius:50%;border:1.3px solid #333}
.search{left:795px;top:155px;width:222px;border-bottom:1px solid #555;font-size:8px;color:#777;padding-bottom:4px;display:flex;justify-content:space-between}
.bottom{left:0;top:2435px;width:1200px;height:98px;background:var(--brand);color:#fff;text-align:center}
.bottom .c{font-size:14px;margin-top:18px}
.bottom .fine{font-size:8px;line-height:11px;width:1090px;margin:8px auto 0}
</style>
</head>
<body>

<!-- header -->
<div class="abs logo">Veltaro</div>
<div class="abs logo-sub">CANADA</div>
<nav class="abs nav">
  <span class="active">Home</span>
  <span>Tanning<span class="caret">⌄</span></span>
  <span>Massage<span class="caret">⌄</span></span>
  <span>Red Light<span class="caret">⌄</span></span>
  <span>Salon Startup</span>
  <span>About Us</span>
  <span>Contact Us</span>
</nav>
<div class="abs phone">
  <svg width="16" height="16" viewBox="0 0 24 24" fill="none" stroke="#ee1c25" stroke-width="2"><path d="M22 16.9v3a2 2 0 0 1-2.2 2 19.8 19.8 0 0 1-8.6-3.1 19.5 19.5 0 0 1-6-6A19.8 19.8 0 0 1 2.1 4.2 2 2 0 0 1 4.1 2h3a2 2 0 0 1 2 1.7c.1 1 .4 1.9.7 2.8a2 2 0 0 1-.5 2.1L8 9.9a16 16 0 0 0 6 6l1.3-1.3a2 2 0 0 1 2.1-.4c.9.3 1.8.6 2.8.7a2 2 0 0 1 1.7 2z"/></svg>
  416.555.0142
</div>
<div class="btn" style="left:1016px;top:24px;width:137px;height:28px;font-size:13px">Request a Catalog</div>

<!-- hero -->
<section class="abs hero">
  <div class="abs hero-visual" role="img" aria-label="Tanning bed, red light bed and water massage bed beside a woman's profile"></div>
  <div class="abs hero-text">
    <div class="light">THE LEADING MANUFACTURER IN</div>
    <div class="big">COMMERCIAL TANNING,</div>
    <div class="big">RED LIGHT <em>AND</em></div>
    <div class="big">WATER MASSAGE THERAPY</div>
  </div>
  <div class="btn" style="left:39px;top:290px;width:128px;height:26px">View Our Products</div>
  <div class="abs counter">01<div class="bar"><i></i></div><span class="last">05</span></div>
</section>
<div class="dots" style="top:543px"><i class="on"></i><i></i><i></i><i></i><i></i></div>

<!-- featured -->
<h2 class="h2" style="top:574px">OUR FEATURED PRODUCTS</h2>
<div class="card tan" role="img" aria-label="Woman in sunglasses relaxing in a tanning bed">TANNING BED</div>
<div class="card hydro" role="img" aria-label="Hydro massage bed in a brick-walled room">HYDRO MASSAGE</div>
<div class="card red" role="img" aria-label="Woman lying under red light therapy">RED LIGHT BEDS</div>

<!-- applications -->
<h2 class="h2" style="top:1099px">ENDLESS INDUSTRY APPLICATIONS</h2>
<div class="app left"><p>nsive<br>line<br>HydroGlide,<br>, housing<br>or<br>mmunity<br>eptional<br>ell-being<br>making it</p></div>
<div class="app center">
  <div class="abs app-img" role="img" aria-label="Friends relaxing in a living room beside a red light bed"></div>
  <div class="abs app-body">
    <h3>HOUSING</h3>
    <p>Distinguish your community by providing a comprehensive range of amenities to your residents. From top-of-the-line commercial tanning equipment to the revolutionary HydroGlide, the world's first and only trackless water massage bed, housing offices can leverage these products as enticing perks or optional amenities to promote wellness within the community and attract prospective residents. By offering such exceptional features, you create an environment that prioritizes well-being and sets your community apart from the competition, making it an irresistible choice for those seeking a vibrant and health-conscious living experience.</p>
  </div>
  <div class="btn" style="left:466px;top:311px;width:107px;height:27px">Learn More</div>
</div>
<div class="app right" role="img" aria-label="Woman in a towel relaxing in a sauna"></div>
<div class="dots" style="top:1581px"><i></i><i class="on"></i><i></i><i></i><i></i></div>

<!-- salon -->
<section class="abs salon">
  <svg class="abs" style="left:0;top:0" width="1200" height="563" viewBox="0 0 1200 563">
    <defs>
      <linearGradient id="salonPhoto" x1="0" y1="0" x2="1" y2="1">
        <stop offset="0" stop-color="#f3eef0"/>
        <stop offset=".5" stop-color="#e9d4c8"/>
        <stop offset="1" stop-color="#aab9da"/>
      </linearGradient>
    </defs>
    <path d="M70 120 C 120 30, 400 45, 640 40 C 900 30, 1130 20, 1160 170 C 1190 330, 1150 500, 1000 520 C 780 545, 560 470, 380 510 C 200 550, 60 520, 55 420 C 50 320, 30 200, 70 120 Z" fill="#ffffff"/>
    <path d="M640 50 C 820 20, 1110 40, 1140 180 C 1175 340, 1150 480, 1010 505 C 850 530, 620 480, 470 500 C 520 400, 560 200, 640 50 Z" fill="url(#salonPhoto)" role="img" aria-label="Smiling woman resting her arms on the edge of a bath"/>
  </svg>
  <div class="abs salon-l1">STARTING A</div>
  <div class="abs salon-l2">SALON <em>OR</em> SPA</div>
  <div class="abs salon-l3">We’ve done it 100s of Times<br>and Will Help You</div>
  <ul class="abs salon-list">
    <li><svg width="12" height="14" viewBox="0 0 12 14"><path d="M2 1l7 6-7 6" fill="none" stroke="#6b77c2" stroke-width="2"/></svg>Space Design</li>
    <li><svg width="12" height="14" viewBox="0 0 12 14"><path d="M2 1l7 6-7 6" fill="none" stroke="#6b77c2" stroke-width="2"/></svg>Review Financing Options</li>
    <li><svg width="12" height="14" viewBox="0 0 12 14"><path d="M2 1l7 6-7 6" fill="none" stroke="#6b77c2" stroke-width="2"/></svg>Starup Marketing</li>
    <li><svg width="12" height="14" viewBox="0 0 12 14"><path d="M2 1l7 6-7 6" fill="none" stroke="#6b77c2" stroke-width="2"/></svg>Times and Will Help You</li>
  </ul>
  <div class="btn" style="left:177px;top:433px;width:138px;height:27px">Request more Info</div>
</section>

<!-- footer -->
<footer class="abs footer">
  <div class="abs f-logo">Veltaro</div>
  <div class="abs f-addr">
    <b class="t">Veltaro Canada</b>
    1180 Maple Crest Road,<br>Lakeview Park, Canada.<br>
    <div style="margin-top:10px;line-height:22.5px">
      <b>Sales:</b> 727-555-0190<br>
      <b>Parts &amp; Services:</b> 800.555.0185<br>
      <b>Main Line:</b> 800.555.0127
    </div>
  </div>
  <div class="abs f-h" style="left:327px;top:34px">Quick Links</div>
  <div class="abs" style="left:419px;top:45px;width:272px;height:1px;background:#555"></div>
  <ul class="abs f-links" style="left:327px;top:68px">
    <li>⇢ Commercial Tanning</li><li>⇢ Wellness Products</li><li>⇢ Replacement Lamps and Parts</li><li>⇢ Salon Startup</li><li>⇢ Financing</li><li>⇢ Privacy Policy</li>
  </ul>
  <ul class="abs f-links" style="left:571px;top:66px">
    <li>⇢ Customer Service</li><li>⇢ About Us</li><li>⇢ Contact Veltaro</li><li>⇢ Blog</li><li>⇢ Terms of Service</li>
  </ul>
  <div class="abs f-h" style="left:794px;top:34px">Stay Connected</div>
  <div class="abs social" aria-label="Social links"><i></i><i></i><i></i><i></i><i></i><i></i></div>
  <div class="abs" style="left:794px;top:120px;font-size:13px">@veltarocanada</div>
  <div class="abs search">Let us help you find what you need
    <svg width="10" height="10" viewBox="0 0 10 10"><circle cx="4" cy="4" r="3" fill="none" stroke="#333"/><path d="M6.3 6.3L9 9" stroke="#333"/></svg></div>
</footer>
<div class="abs bottom">
  <div class="c">© 2023 Veltaro Canada. All Rights Reserved</div>
  <div class="fine">Tanning 510(k):K000000 • Contraindication: This Product Is Contraindicated For Use On Persons Under The Age Of 18 Years. "Contraindication: This Product Must Not Be Used If Skin Lesions Or Open Wounds Are Present." "Warning: This Product Should Not Be Used On Individuals Who Have Had Skin Cancer Or Have A Family History Of Skin Cancer." "Warning: Persons Repeatedly Exposed To UV Radiation Should Be Regularly Evaluated For Skin Cancer."</div>
</div>
</body>
</html>
```